VELMOR Website Design

We need a website designed for our company VELMOR. We are a luxury lifestyle club that will provide benefits and services for our members. The site should be clean & sleek, preferably using black and white (or darker colors). (example sites: stravenhall.example, plinth.example)

Here is a link of a sample page I did using wix. (https://dunmere7.sitehostly.example/mysite) This can be used to get a general idea.

Target Market(s)

Upper Middle Class in the United States

Number of Pages Required

5+ page

Font styles to use
Sans Serif
Other font styles liked:
• Arial (or other similar fonts)

Requirements
Must have
• A clean design that is eye-catching and speaks to our company.
Nice to have
• Ideas for copy.

```html
<!DOCTYPE html>
<html lang="en">
<head>
<meta charset="utf-8">
<title>VELMOR — A Members Only Lifestyle Club</title>
<link rel="stylesheet" href="https://fonts.googleapis.com/css2?family=Kumbh+Sans:wght@700;800&family=Encode+Sans+Condensed:wght@300&family=Open+Sans:wght@400;600&display=swap">
<style>
:root{
  --ink:#0b0b0b;
  --paper:#ffffff;
  --night:#0e0e0e;
  --muted:#8a8a8a;
  --faint:#3a3a3a;
  --text:#1a1a1a;
}
*{box-sizing:border-box;margin:0;padding:0}
html,body{width:1200px;height:2894px;overflow:hidden}
body{position:relative;background:var(--paper);color:var(--text);font-family:"Open Sans",Arial,sans-serif}
.abs{position:absolute}
.center{left:0;width:1200px;text-align:center}

/* Hero */
.hero{left:0;top:0;width:1200px;height:700px;clip-path:polygon(0 0,1200px 0,1200px 642px,0 698px);
  background:radial-gradient(ellipse at 60% 30%,#6b6b6b 0%,#3d3d3d 35%,#1c1c1c 75%,#111 100%)}
.nav{top:0;left:0;width:1200px;height:100px}
.brand{left:100px;top:28px;font-family:"Kumbh Sans",Arial,sans-serif;font-weight:800;font-size:36px;color:var(--paper);letter-spacing:1px}
.nav-link{top:38px;font-size:14.5px;color:var(--paper);transform:translateX(-50%);white-space:nowrap;letter-spacing:.2px}
.nav-link.current::after{content:"";position:absolute;left:-2px;right:-2px;bottom:-9px;height:2px;background:var(--paper)}
.btn-login{left:841px;top:33px;width:81px;height:34px;border:1.5px solid #cfcfcf;color:var(--paper);font-size:14px;display:flex;align-items:center;justify-content:center}
.btn-join{left:936px;top:33px;width:165px;height:34px;background:var(--paper);color:var(--ink);font-size:14px;font-weight:600;display:flex;align-items:center;justify-content:center}
.hero-title{top:272px;font-family:"Kumbh Sans",Arial,sans-serif;font-weight:700;font-size:57px;color:var(--paper);text-shadow:0 2px 8px rgba(0,0,0,.5)}
.dots{top:606px;left:0;width:1200px;display:flex;justify-content:center;gap:16px}
.dots span{width:13px;height:13px;border-radius:50%;background:rgba(255,255,255,.45)}
.dots span:first-child{background:var(--paper)}

/* Headings */
.heading{font-family:"Kumbh Sans",Arial,sans-serif;font-weight:700;font-size:38px;line-height:1}
.rule{left:564px;width:72px;height:3px;background:var(--ink)}
.rule.light{background:var(--paper)}
.copy{left:150px;width:900px;text-align:center;font-size:16px;line-height:24px;color:var(--text)}
.btn-apply{left:534px;width:133px;height:45px;background:var(--ink);color:var(--paper);font-size:18px;letter-spacing:.5px;display:flex;align-items:center;justify-content:center}

.tagline{top:838px;font-family:"Encode Sans Condensed",Arial,sans-serif;font-weight:300;font-size:33px;color:var(--text)}

/* Services */
.services{left:0;top:1212px;width:1200px;height:806px;clip-path:polygon(0 0,1200px 0,1200px 806px,0 752px);
  background:linear-gradient(180deg,#1f1f1f 0%,#151515 45%,#0c0c0c 100%)}
.service{width:260px;transform:translateX(-50%);text-align:center}
.service .ring{width:100px;height:100px;margin:0 auto;border:1.5px solid #6a6a6a;border-radius:50%;display:flex;align-items:center;justify-content:center}
.service .label{margin-top:14px;font-size:14px;font-weight:600;color:var(--paper);letter-spacing:.2px}

/* Footer */
.footer{left:0;top:2410px;width:1200px;height:484px;background:var(--night);clip-path:polygon(0 46px,1200px 0,1200px 484px,0 484px)}
.footer-nav{top:2473px;left:0;width:1200px;display:flex;justify-content:center;gap:30px;font-size:10px;color:var(--faint)}
.signup{top:2590px;font-size:16px;color:#6e6e6e}
.btn-subscribe{left:529px;top:2633px;width:142px;height:48px;border:1.5px solid #bdbdbd;color:var(--paper);font-size:18px;display:flex;align-items:center;justify-content:center}
.social{top:2725px;left:0;width:1200px;display:flex;justify-content:center;gap:5px}
.social span{width:36px;height:36px;border:1.5px solid #bdbdbd;border-radius:50%}
.footer-line{left:100px;top:2803px;width:1000px;height:1px;background:#262626}
.copyright{top:2838px;font-size:13px;color:#cfcfcf}
</style>
</head>
<body>

<div class="abs hero" role="img" aria-label="Black and white photograph of a bartender pouring a cocktail from a shaker into a glass"></div>

<header class="abs nav">
  <div class="abs brand">VELMOR</div>
  <a class="abs nav-link current" style="left:401px">HOME</a>
  <a class="abs nav-link" style="left:486px">ABOUT</a>
  <a class="abs nav-link" style="left:627px">SERVICES AND BENFITS</a>
  <a class="abs nav-link" style="left:777px">CONTACT</a>
  <a class="abs btn-login">LOG IN</a>
  <a class="abs btn-join">BECOME A MEMBER</a>
</header>

<h1 class="abs center hero-title">A Members Only Lifestyle Club</h1>
<div class="dots abs"><span></span><span></span><span></span><span></span></div>

<section>
  <h2 class="abs center heading" style="top:762px;color:var(--ink)">About VELMOR</h2>
  <div class="abs rule" style="top:815px"></div>
  <p class="abs center tagline">The ultimate full service lifestyle club</p>
  <p class="abs copy" style="top:900px">VELMOR was formed to bring the best services, experiences, and exclusive opportunities to our members. With everything from private member events to private jet travel, the perks of being a VELMOR member are unmatched. Professional athletes, artists, musicians, corporate professionals: Our members come from diverse backgrounds.</p>
  <p class="abs copy" style="top:995px">Comprehensive services like 24/7 concierge, accountants, attorneys, private advisers, planners, investment advisors and more.</p>
  <a class="abs btn-apply" style="top:1073px">APPLY</a>
</section>

<section>
  <div class="abs services" role="img" aria-label="Dark black and white photograph of runners on a waterfront path"></div>
  <h2 class="abs center heading" style="top:1305px;color:var(--paper)">Services and Benefits</h2>
  <div class="abs rule light" style="top:1349px"></div>

  <div class="abs service" style="left:340px;top:1405px">
    <div class="ring"><svg width="46" height="46" viewBox="0 0 46 46" fill="none" stroke="#fff" stroke-width="2"><path d="M10 5h20l6 6v30H10z"/><path d="M15 16h14M15 22h14M15 28h9"/><path d="M26 38l12-12 3 3-12 12h-3z"/></svg></div>
    <div class="label">ACCOUNTING SERVICES</div>
  </div>
  <div class="abs service" style="left:600px;top:1405px">
    <div class="ring"><svg width="46" height="46" viewBox="0 0 46 46" fill="none" stroke="#fff" stroke-width="2"><path d="M6 40h34"/><path d="M10 40V30h5v10M19 40V24h5v16M28 40V18h5v22"/><path d="M8 24l10-8 7 4 13-12M32 8h6v6"/></svg></div>
    <div class="label">INVESTMENT SERVICES</div>
  </div>
  <div class="abs service" style="left:857px;top:1405px">
    <div class="ring"><svg width="46" height="46" viewBox="0 0 46 46" fill="none" stroke="#fff" stroke-width="2"><path d="M23 6v32M14 40h18M10 12h26"/><path d="M10 12l-6 13h12zM36 12l-6 13h12z"/><path d="M4 25a6 4 0 0 0 12 0M30 25a6 4 0 0 0 12 0"/></svg></div>
    <div class="label">LAWYER SERVICES</div>
  </div>

  <div class="abs service" style="left:340px;top:1567px">
    <div class="ring"><svg width="46" height="46" viewBox="0 0 46 46" fill="none" stroke="#fff" stroke-width="2"><path d="M8 8h30v6H8zM10 14v26h26V14"/><path d="M14 20h6v6h-6zM26 20h6v6h-6zM19 40V31h8v9"/></svg></div>
    <div class="label">REAL ESTATE SERVICES</div>
  </div>
  <div class="abs service" style="left:600px;top:1567px">
    <div class="ring"><svg width="46" height="46" viewBox="0 0 46 46" fill="none" stroke="#fff" stroke-width="2"><path d="M3 18l8-6 6 2 6-3 6 3 6-2 8 6"/><path d="M11 12l-5 12 6 6M35 12l5 12-6 6"/><path d="M17 20l7 7a2 2 0 0 1-3 3l-4-4M21 30l3 3a2 2 0 0 0 3-3M24 33l1 1a2 2 0 0 0 3-3l-6-6M28 31a2 2 0 0 0 3-3l-8-8"/></svg></div>
    <div class="label">24/7 CONCIERGE</div>
  </div>
  <div class="abs service" style="left:857px;top:1567px">
    <div class="ring"><svg width="46" height="46" viewBox="0 0 46 46" fill="none" stroke="#fff" stroke-width="2"><path d="M37 6c2 0 3 1 3 3l-9 9 4 17-3 3-7-13-7 7v5l-3 2-2-6-6-2 2-3h5l7-7-13-7 3-3 17 4 9-9z"/></svg></div>
    <div class="label">PRIVATE JET TRAVEL</div>
  </div>

  <div class="abs service" style="left:340px;top:1729px">
    <div class="ring"><svg width="46" height="46" viewBox="0 0 46 46" fill="none" stroke="#fff" stroke-width="2"><path d="M7 10h32v30H7zM7 18h32M15 5v8M31 5v8"/><path d="M13 24h4M21 24h4M29 24h4M13 30h4M21 30h4M29 30h4M13 35h4M21 35h4"/></svg></div>
    <div class="label">EVENT ACCESS</div>
  </div>
  <div class="abs service" style="left:600px;top:1729px">
    <div class="ring"><svg width="46" height="46" viewBox="0 0 46 46" fill="none" stroke="#fff" stroke-width="2"><path d="M10 14l8 3-2 9a4 4 0 0 1-7-3zM36 14l-8 3 2 9a4 4 0 0 0 7-3z"/><path d="M12 28l-3 10M6 38h6M34 28l3 10M34 38h6"/><path d="M23 4v5M16 6l3 4M30 6l-3 4"/></svg></div>
    <div class="label">PRIVATE EVENTS</div>
  </div>
  <div class="abs service" style="left:857px;top:1729px">
    <div class="ring"><svg width="46" height="46" viewBox="0 0 46 46" fill="none" stroke="#fff" stroke-width="2"><path d="M6 14h34v24H6zM17 14V9h12v5M6 24h34M20 22h6v5h-6z"/></svg></div>
    <div class="label">EXPERIENCES</div>
  </div>
</section>

<section>
  <h2 class="abs center heading" style="top:2069px;color:var(--ink)">We Are VELMOR</h2>
  <div class="abs rule" style="top:2122px"></div>
  <p class="abs copy" style="top:2148px;left:230px;width:740px">Built in the image of a"Multi-Family Office", VELMOR provides members with access to just about any service, experience, and event desirable.</p>
  <p class="abs copy" style="top:2218px">VELMOR is truly the most exclusive lifestyle club out there.</p>
  <a class="abs btn-apply" style="top:2290px">APPLY</a>
</section>

<footer>
  <div class="abs footer"></div>
  <nav class="footer-nav abs"><span>Home</span><span>About</span><span>Services and Benefits</span><span>Contact</span></nav>
  <h2 class="abs center heading" style="top:2528px;color:var(--paper)">Contact Us</h2>
  <div class="abs rule light" style="top:2572px"></div>
  <p class="abs center signup">sign up with your email address to receive news and updates.</p>
  <a class="abs btn-subscribe">SUBSCRIBE</a>
  <div class="social abs" aria-label="Social links"><span></span><span></span><span></span><span></span><span></span></div>
  <div class="abs footer-line"></div>
  <p class="abs center copyright">© 2018 VELMOR . All rights reserved.</p>
</footer>

</body>
</html>
```